Folded A4 flyer for design&construction company

Folded A4 flyer needed. Keywords: elegant, stylish
our website www.dorvika.ae

Industry/Entity Type

Construction

```html
<!DOCTYPE html>
<html lang="en">
<head>
<meta charset="utf-8">
<title>Dorvika – Folded Flyer</title>
<link rel="stylesheet" href="https://fonts.googleapis.com/css2?family=Lato:wght@400;700&display=swap">
<style>
  :root {
    --stage: #ececec;
    --paper: #ffffff;
    --ink: #1c1c1c;
    --text: #3a3a3a;
    --gold-dark: #a87a0c;
    --gold: #d9aa17;
    --gold-light: #f6d34a;
    --gold-text: #a6780e;
    --rule: #c9c9c9;
  }
  * { box-sizing: border-box; margin: 0; padding: 0; }
  html, body { width: 1200px; height: 1200px; overflow: hidden; }
  body {
    background: var(--stage);
    font-family: "Lato", sans-serif;
    color: var(--text);
    position: relative;
  }
  .spread {
    position: absolute;
    left: 180px; top: 303px;
    width: 840px; height: 594px;
    display: flex;
    box-shadow: 0 18px 40px rgba(0,0,0,0.18);
  }
  .page {
    position: relative;
    width: 420px; height: 594px;
    background: var(--paper);
    overflow: hidden;
  }
  .band-black { position: absolute; left: 0; right: 0; background: var(--ink); }
  .band-gold {
    position: absolute; left: 0; right: 0;
    background: linear-gradient(90deg, var(--gold-dark), var(--gold-light) 45%, var(--gold) 70%, var(--gold-dark));
  }

  /* Cover */
  .cover .band-black.top { top: 0; height: 28px; }
  .cover .hero-fade {
    position: absolute; left: 0; right: 0; top: 28px; height: 250px;
    background: linear-gradient(180deg, #d9d9d9 0%, #eeeeee 55%, #ffffff 100%);
  }
  .brand-name {
    font-family: "Lato", sans-serif;
    font-weight: 400;
    color: var(--ink);
    letter-spacing: 1px;
    text-align: center;
  }
  .cover .brand-name {
    position: absolute; top: 250px; left: 0; right: 0;
    font-size: 40px;
  }
  .quote-block { position: absolute; top: 408px; left: 40px; right: 40px; text-align: center; }
  .quote-rule { display: flex; align-items: center; gap: 10px; margin-bottom: 14px; }
  .quote-rule span { flex: 1; height: 1px; background: var(--rule); }
  .quote-rule i { width: 6px; height: 6px; background: var(--gold); transform: rotate(45deg); }
  .quote {
    font-weight: 700; font-size: 17px; color: var(--gold-text);
  }
  .cover .band-gold.bottom { bottom: 12px; height: 30px; }
  .cover .band-black.bottom { bottom: 0; height: 12px; }

  /* Inside */
  .inside .band-gold.top { top: 0; height: 22px; }
  .inside .hero {
    position: absolute; left: 0; right: 0; top: 22px; height: 232px;
    background: linear-gradient(160deg, #ddd6cb 0%, #f3eee6 45%, #c9b9a2 100%);
  }
  .inside .brand-name {
    position: absolute; top: 50px; left: 150px; width: 150px;
    font-size: 30px;
  }
  .intro-rule { position: absolute; top: 268px; left: 60px; right: 60px; }
  .intro {
    position: absolute; top: 284px; left: 40px; right: 40px;
    font-size: 9.5px; line-height: 1.35; text-align: center; color: var(--text);
  }
  .intro p + p { margin-top: 6px; }
  .gallery {
    position: absolute; top: 378px; left: 36px; right: 36px;
    display: flex; justify-content: space-between;
  }
  .gallery div { width: 108px; height: 70px; }
  .gallery .g1 { background: linear-gradient(135deg, #b68a5a, #e6cfa8); }
  .gallery .g2 { background: linear-gradient(135deg, #4a4a50, #a8a8b0); }
  .gallery .g3 { background: linear-gradient(135deg, #7a5a30, #e9c98a); }
  .cta {
    position: absolute; top: 470px; left: 0; right: 0; text-align: center;
    font-weight: 700; font-size: 11px; color: var(--gold);
  }
  .contact-line {
    position: absolute; left: 0; right: 0; text-align: center;
    font-size: 9px; color: var(--ink);
  }
  .contact-line.phone { top: 488px; }
  .contact-line.address { top: 508px; display: flex; justify-content: center; align-items: center; gap: 6px; }
  .contact-line .sep { color: var(--gold); }
  .contact-line svg { width: 9px; height: 9px; fill: var(--gold); }
  .inside .band-gold.bottom { bottom: 22px; height: 5px; }
  .inside .band-black.bottom { bottom: 0; height: 22px; }
</style>
</head>
<body>
  <main class="spread">
    <section class="page cover">
      <div class="band-black top"></div>
      <div class="hero-fade" role="img" aria-label="Faded photograph of a bright modern interior"></div>
      <div class="brand-name">DORVIKA</div>
      <div class="quote-block">
        <div class="quote-rule"><span></span><i></i><span></span></div>
        <p class="quote">Quality is not an act, it is a habit – Elara Voss</p>
      </div>
      <div class="band-gold bottom"></div>
      <div class="band-black bottom"></div>
    </section>

    <section class="page inside">
      <div class="band-gold top"></div>
      <div class="hero" role="img" aria-label="Photograph of a luxurious bright bathroom with freestanding tub"></div>
      <div class="brand-name">DORVIKA</div>
      <div class="quote-rule intro-rule"><span></span><i></i><span></span></div>
      <div class="intro">
        <p>We believe in quality beginnings and flawless finishes. We are a team of creative designers and constructors with years of experience and expertise in providing complete interior design and construction services.</p>
        <p>Our unique designing prowess is complemented by our unflinching commitment to quality construction. Our team specializes in classic and contemporary high quality construction in Dubai for commercial and residential projects.</p>
      </div>
      <div class="gallery">
        <div class="g1" role="img" aria-label="Photograph of a warm classic living room"></div>
        <div class="g2" role="img" aria-label="Photograph of a modern dining area"></div>
        <div class="g3" role="img" aria-label="Photograph of a softly lit curved lounge"></div>
      </div>
      <p class="cta">GET A FREE QUOTE TODAY!</p>
      <p class="contact-line phone">
        <svg viewBox="0 0 10 10"><path d="M2 1l2 2-1 1c.5 1.2 1.8 2.5 3 3l1-1 2 2-1.5 1.5C4 9 1 6 .5 2.5z"/></svg>
        800 – DORVIKA <span class="sep">/</span> CONTACT@DORVIKA.AE
      </p>
      <p class="contact-line address">
        <svg viewBox="0 0 10 10"><path d="M5 0a3.5 3.5 0 0 1 3.5 3.5C8.5 6 5 10 5 10S1.5 6 1.5 3.5A3.5 3.5 0 0 1 5 0zm0 2a1.5 1.5 0 1 0 0 3 1.5 1.5 0 0 0 0-3z"/></svg>
        Dorvika LLC, Palm Crest Tower, Office 1207, Business Bay, Dubai
        <span class="sep">|</span>
        www.dorvika.ae
      </p>
      <div class="band-gold bottom"></div>
      <div class="band-black bottom"></div>
    </section>
  </main>
</body>
</html>
```